Brightway Haul & Upkeep Services, are a company that offers a 'one stop shop' pre-move clean up a

I have already selected a logo which I would like on the front of the business cards along with phone numbers, web address and email which are:
0487650392
www.brightwayhaul.com.au
brightwayhaulandupkeep@mailbox.example

On the back of the card I would like to list some of the types of service we offer (clean - move - repairs/maintenance) which are:
CLEAN - windows, gutters, solar panels, driveways/paths, carpets.
MOVE - Small/medium size house/office moves, large item pick-up & delivery, yard clean-up and removal.
General maintenance and repairs.

I would like the blue logo on a gray background.

Thanks

```html
<!DOCTYPE html>
<html lang="en">
<head>
<meta charset="utf-8">
<title>Brightway Haul &amp; Upkeep Services – Business Card</title>
<link href="https://fonts.googleapis.com/css2?family=Open+Sans:wght@400;600;700;800&display=swap" rel="stylesheet">
<style>
  :root {
    --brand-blue: #2f7fc6;
    --brand-blue-deep: #1f6fb8;
    --ink: #1a1a1a;
    --swoosh: #161616;
    --silver-light: #f4f4f4;
    --silver-mid: #d6d6d6;
    --silver-dark: #b9b9b9;
    --page: #ebe8e3;
    --white: #ffffff;
  }
  * { box-sizing: border-box; margin: 0; padding: 0; }
  html, body { width: 1016px; height: 1200px; overflow: hidden; }
  body {
    background: var(--page);
    font-family: "Open Sans", Arial, sans-serif;
    position: relative;
  }
  .card {
    position: absolute;
    left: 36px;
    width: 944px;
    height: 536px;
    border-radius: 30px;
    overflow: hidden;
    background: radial-gradient(ellipse at 55% 35%, var(--silver-light) 0%, var(--silver-mid) 60%, var(--silver-dark) 100%);
    box-shadow: 0 2px 6px rgba(0,0,0,.18);
  }
  .card--front { top: 38px; }
  .card--back { top: 624px; height: 538px; }

  .card__wave { position: absolute; inset: 0; width: 100%; height: 100%; }

  .brand-name {
    position: absolute;
    color: var(--brand-blue);
    font-weight: 800;
    text-transform: uppercase;
    line-height: 1.05;
  }
  .card--front .brand-name {
    left: 0; right: 0; top: 96px;
    text-align: center;
    padding-left: 60px;
  }
  .brand-name__main { display: block; font-size: 66px; letter-spacing: 1px; }
  .brand-name__sub { display: block; font-size: 34px; letter-spacing: 1px; }

  .contact {
    position: absolute;
    color: var(--white);
    font-size: 23px;
    display: flex;
    align-items: center;
    gap: 10px;
  }
  .contact svg { width: 18px; height: 18px; fill: var(--white); flex: none; }
  .contact--phone { left: 116px; top: 468px; }
  .contact--email { left: 400px; top: 428px; }
  .contact--web { left: 400px; top: 488px; }
  .contact-divider {
    position: absolute;
    left: 374px; top: 420px;
    width: 3px; height: 96px;
    background: var(--white);
    border-radius: 2px;
  }

  .card--back .brand-name { left: 50px; top: 60px; }
  .card--back .brand-name__main { font-size: 54px; }
  .card--back .brand-name__sub { font-size: 28px; }

  .abn {
    position: absolute;
    left: 110px; top: 222px;
    font-size: 30px;
    color: var(--ink);
    letter-spacing: .5px;
  }
  .services-title {
    position: absolute;
    right: 34px; top: 278px;
    font-size: 36px;
    font-weight: 600;
    color: var(--brand-blue);
  }
  .service {
    position: absolute;
    right: 34px;
    display: flex;
    gap: 14px;
    font-size: 23px;
    color: var(--ink);
    line-height: 1.45;
  }
  .service__label {
    color: var(--brand-blue);
    font-weight: 700;
    font-size: 26px;
    line-height: 1.3;
  }
  .service--clean { top: 366px; }
  .service--move { top: 410px; }
  .service--move .service__text { text-align: right; }
  .services-footer {
    position: absolute;
    right: 34px; top: 478px;
    font-size: 28px;
    font-weight: 600;
    letter-spacing: 2.5px;
    color: var(--brand-blue);
  }
</style>
</head>
<body>

<section class="card card--front" aria-label="Business card front">
  <svg class="card__wave" viewBox="0 0 944 536" preserveAspectRatio="none" aria-hidden="true">
    <defs>
      <linearGradient id="blue-band" x1="0" y1="0" x2="0" y2="1">
        <stop offset="0" stop-color="#3588d0"/>
        <stop offset="1" stop-color="#1f6fb8"/>
      </linearGradient>
    </defs>
    <path d="M0,262 C260,330 520,420 944,278 L944,536 L0,536 Z" fill="url(#blue-band)"/>
    <path d="M0,206 C210,250 470,392 770,384 C500,380 250,316 0,246 Z" fill="#161616"/>
  </svg>

  <h1 class="brand-name">
    <span class="brand-name__main">Brightway Haul</span>
    <span class="brand-name__sub">&amp; Upkeep Services</span>
  </h1>

  <p class="contact contact--phone">
    <svg viewBox="0 0 24 24" aria-hidden="true"><path d="M6.6 10.8a15 15 0 0 0 6.6 6.6l2.2-2.2a1 1 0 0 1 1-.25 11.4 11.4 0 0 0 3.6.57 1 1 0 0 1 1 1V20a1 1 0 0 1-1 1A17 17 0 0 1 3 4a1 1 0 0 1 1-1h3.5a1 1 0 0 1 1 1c0 1.25.2 2.46.57 3.6a1 1 0 0 1-.25 1z"/></svg>
    0487650392
  </p>
  <span class="contact-divider" aria-hidden="true"></span>
  <p class="contact contact--email">
    <svg viewBox="0 0 24 24" aria-hidden="true"><path d="M3 5h18a1 1 0 0 1 1 1v12a1 1 0 0 1-1 1H3a1 1 0 0 1-1-1V6a1 1 0 0 1 1-1zm9 7.5L20 7H4z"/></svg>
    brightwayhaulandupkeep@mailbox.example
  </p>
  <p class="contact contact--web">
    <svg viewBox="0 0 24 24" aria-hidden="true"><path d="M12 2a10 10 0 1 0 0 20 10 10 0 0 0 0-20zm6.9 6h-3a15 15 0 0 0-1.3-3.9A8 8 0 0 1 18.9 8zM12 4c.9 1.2 1.6 2.6 2 4h-4c.4-1.4 1.1-2.8 2-4zM4.3 14a8 8 0 0 1 0-4h3.4a16 16 0 0 0 0 4zm.8 2h3a15 15 0 0 0 1.3 3.9A8 8 0 0 1 5.1 16zm3-8h-3a8 8 0 0 1 4.3-3.9A15 15 0 0 0 8.1 8zM12 20c-.9-1.2-1.6-2.6-2-4h4c-.4 1.4-1.1 2.8-2 4zm2.3-6H9.7a14 14 0 0 1 0-4h4.6a14 14 0 0 1 0 4zm.3 5.9a15 15 0 0 0 1.3-3.9h3a8 8 0 0 1-4.3 3.9zm1.7-5.9a16 16 0 0 0 0-4h3.4a8 8 0 0 1 0 4z"/></svg>
    www.brightwayhaul.com.au
  </p>
</section>

<section class="card card--back" aria-label="Business card back">
  <h2 class="brand-name">
    <span class="brand-name__main">Brightway Haul</span>
    <span class="brand-name__sub">&amp; Upkeep Services</span>
  </h2>
  <p class="abn">ABN 48105927316</p>

  <h3 class="services-title">Services we offer</h3>
  <p class="service service--clean">
    <span class="service__label">CLEAN:</span>
    <span class="service__text">Windows, Gutters, Solar Panels, Driveways/paths, Carpets.</span>
  </p>
  <p class="service service--move">
    <span class="service__label">MOVE:</span>
    <span class="service__text">Small/medium Size House/office Moves, Large Item Pick-up<br>&amp; Delivery, Yard Clean-up And Removal.</span>
  </p>
  <p class="services-footer">General maintenance and repairs.</p>
</section>

</body>
</html>
```